Web Developer Needs a Business Card Design

I need a personal business card design that represents me as a web developer for potential employers. I would like the background to be a dark color on the front for contrast with my logo and name. The back will have all my information along with a smaller version of the logo. I want something with a modern look and feel, not too conservative. This will be used for potential employers and freelance work.

Industry/Entity Type

Business

Contact Information for Business Card

Front should have my logo and name. The back should have all my personal information which would include: name: Tom Varulek, phone: 570-614-3098, email: tomvarulek@quillbox.net, website url: www.tomvarulek.net, logo, web developer.

Font styles to use
Sans Serif

Requirements
Must have
• Must include my logo. The color palette base color will be the logo color.

```html
<!DOCTYPE html>
<html lang="en">
<head>
<meta charset="utf-8">
<title>Tom Varulek – Business Card</title>
<link rel="stylesheet" href="https://fonts.googleapis.com/css2?family=Roboto:wght@400;500;700&display=swap">
<style>
  :root {
    --stage: #9d9b9b;
    --brand-teal: #5ce0c2;
    --card-dark: #0c0c0d;
    --card-dark-soft: #1a1b1c;
    --card-light: #f7f7f6;
    --ink: #1f2022;
    --band-dark: #141517;
    --divider: #e2e2e0;
    --white: #ffffff;
  }
  * { margin: 0; padding: 0; box-sizing: border-box; }
  html, body {
    width: 1200px; height: 1200px; overflow: hidden;
    background: var(--stage);
    font-family: "Roboto", Arial, sans-serif;
  }
  .canvas { position: relative; width: 1200px; height: 1200px; }

  .card {
    position: absolute; width: 714px; height: 420px;
    border-radius: 24px; overflow: hidden;
  }

  /* Front */
  .card-front { left: 238px; top: 117px; background: var(--card-dark); }
  .front-photo {
    position: absolute; inset: 0;
    background: radial-gradient(ellipse at 30% 40%, var(--card-dark-soft) 0%, var(--card-dark) 70%);
  }
  .front-brand {
    position: absolute; left: 0; right: 0; top: 186px;
    display: flex; align-items: center; justify-content: center; gap: 16px;
    color: var(--brand-teal); font-weight: 700; font-size: 40px;
  }
  .brand-dot {
    width: 34px; height: 34px; border-radius: 50%;
    background: var(--brand-teal);
  }

  /* Back */
  .card-back { left: 230px; top: 644px; height: 418px; background: var(--card-light); }
  .back-brand {
    position: absolute; left: 40px; width: 285px; top: 162px;
    display: flex; align-items: center; justify-content: center; gap: 12px;
    color: var(--brand-teal); font-weight: 700; font-size: 30px;
  }
  .back-brand .brand-dot { width: 26px; height: 26px; }
  .divider {
    position: absolute; left: 347px; top: 44px; width: 1px; height: 276px;
    background: var(--divider);
  }
  .contact { position: absolute; left: 410px; top: 106px; color: var(--ink); }
  .contact-name { font-size: 31px; font-weight: 700; color: var(--brand-teal); line-height: 36px; }
  .contact-role { font-size: 18px; margin-top: 6px; }
  .contact-list { list-style: none; margin-top: 26px; font-size: 19px; }
  .contact-list li { display: flex; align-items: center; height: 29px; }
  .contact-list svg { width: 18px; height: 18px; margin-right: 21px; fill: var(--brand-teal); }

  .back-bands { position: absolute; left: 0; bottom: 0; width: 714px; height: 56px; }
  .website {
    position: absolute; left: 410px; bottom: 16px;
    color: var(--white); font-size: 19px;
  }
</style>
</head>
<body>
<div class="canvas">

  <section class="card card-front">
    <div class="front-photo" role="img" aria-label="Dark desk photo with keyboard, tablet and notebook"></div>
    <div class="front-brand"><span class="brand-dot"></span><span>Tom Varulek</span></div>
  </section>

  <section class="card card-back">
    <div class="back-brand"><span class="brand-dot"></span><span>Tom Varulek</span></div>
    <div class="divider"></div>
    <div class="contact">
      <h1 class="contact-name">Tom Varulek</h1>
      <p class="contact-role">Web Developer</p>
      <ul class="contact-list">
        <li>
          <svg viewBox="0 0 24 24" aria-hidden="true"><path d="M3 8c0-3 4-5 9-5s9 2 9 5v2h-5V8H8v2H3zM6 12h12l3 8H3z"/></svg>
          570-614-3098
        </li>
        <li>
          <svg viewBox="0 0 24 24" aria-hidden="true"><path d="M2 5h20v14H2zm2 2v.5l8 5 8-5V7z"/></svg>
          tomvarulek@quillbox.net
        </li>
      </ul>
    </div>
    <svg class="back-bands" viewBox="0 0 714 56" aria-hidden="true">
      <rect x="0" y="29" width="370" height="27" fill="var(--brand-teal)"/>
      <polygon points="378,0 714,0 714,56 342,56" fill="var(--band-dark)"/>
    </svg>
    <p class="website">www.tomvarulek.net</p>
  </section>

</div>
</body>
</html>
```